business card

Business card for new business.
Red and black corporate colors.
Card can have an Indsutrial feel to it. Feel free to add Rust, Bolted steel, or graphics as you see fit. We provide highly specialized services to the below mentioned industries.
Keep information out of corners so that if I want I can choose rounded corners.
Information
- front. name - title - phone - email
- Rear
Refining - Rail - Infrastructure - Mining - Energy
Calgary - Edmonton - Fort McMurray - Revelstoke - Vancouver

```html
<!DOCTYPE html>
<html lang="en">
<head>
<meta charset="utf-8">
<title>Ironvale business card</title>
<link rel="stylesheet" href="https://fonts.googleapis.com/css2?family=Arimo:wght@400;700&display=swap">
<style>
  :root {
    --stage: #e9e6e1;
    --card-dark: #262729;
    --card-dark-edge: #1b1c1e;
    --card-light: #f4f4f2;
    --brand-red: #e0202f;
    --ink-light: #ffffff;
    --ink-muted: #d8d8d8;
    --ink-grey: #8a8a8a;
    --ink-dark: #3b3b3b;
  }
  * { box-sizing: border-box; margin: 0; padding: 0; }
  html, body { width: 1200px; height: 911px; overflow: hidden; }
  body {
    background: var(--stage);
    font-family: "Arimo", Arial, sans-serif;
    position: relative;
  }
  .card {
    position: absolute;
    border-radius: 14px;
    box-shadow: 0 10px 28px rgba(0,0,0,0.22);
  }
  /* Front: dark vertical card */
  .card-front {
    left: 110px; top: 170px;
    width: 350px; height: 600px;
    background: linear-gradient(160deg, #2e2f31 0%, var(--card-dark) 55%, var(--card-dark-edge) 100%);
    color: var(--ink-light);
    text-align: center;
    padding-top: 86px;
  }
  .person-name {
    font-weight: 700; font-size: 24px; letter-spacing: 0.5px;
  }
  .person-title {
    font-size: 15px; color: var(--ink-muted); margin-top: 4px; letter-spacing: 0.5px;
  }
  .contact-list { list-style: none; margin-top: 22px; }
  .contact-item { margin-bottom: 10px; font-size: 16px; color: var(--ink-light); }
  .contact-icon { display: block; margin: 0 auto 4px; width: 12px; height: 12px; }
  .front-brand {
    margin-top: 58px;
    font-weight: 700; font-size: 44px; color: var(--brand-red);
    letter-spacing: 2px;
  }
  /* Back: white horizontal card */
  .card-back {
    left: 500px; top: 290px;
    width: 600px; height: 350px;
    background: var(--card-light);
    padding: 92px 0 0 120px;
  }
  .back-brand {
    display: flex; align-items: center; gap: 14px;
  }
  .brand-square {
    width: 30px; height: 30px; background: var(--brand-red);
  }
  .back-brand-name {
    font-weight: 700; font-size: 56px; color: var(--ink-grey); letter-spacing: 3px;
  }
  .service-lines { margin-top: 26px; color: var(--ink-dark); font-size: 16px; line-height: 1.5; }
  .sep { color: var(--brand-red); padding: 0 3px; }
</style>
</head>
<body>
  <section class="card card-front" aria-label="Card front">
    <h1 class="person-name">DANIEL REYES</h1>
    <p class="person-title">CEO/FOUNDER</p>
    <ul class="contact-list">
      <li class="contact-item">
        <svg class="contact-icon" viewBox="0 0 12 12" aria-hidden="true"><path d="M2 1 L4.5 1 L5 4 L3.6 5 C4.4 6.8 5.4 7.8 7 8.4 L8 7 L11 7.5 L11 10 C6 11 1 6 2 1 Z" fill="var(--brand-red)"/></svg>
        555 014 2290
      </li>
      <li class="contact-item">
        <svg class="contact-icon" viewBox="0 0 12 12" aria-hidden="true"><rect x="1" y="2.5" width="10" height="7" rx="1" fill="var(--brand-red)"/><path d="M1.5 3 L6 6.5 L10.5 3" stroke="var(--card-dark)" stroke-width="1" fill="none"/></svg>
        info@ironvale.com
      </li>
      <li class="contact-item">
        <svg class="contact-icon" viewBox="0 0 12 12" aria-hidden="true"><circle cx="6" cy="6" r="5" fill="var(--brand-red)"/><path d="M1 6 H11 M6 1 C3.5 3.5 3.5 8.5 6 11 M6 1 C8.5 3.5 8.5 8.5 6 11" stroke="var(--card-dark)" stroke-width="0.8" fill="none"/></svg>
        www.ironvale.com
      </li>
    </ul>
    <p class="front-brand">IRONVALE</p>
  </section>

  <section class="card card-back" aria-label="Card back">
    <div class="back-brand">
      <span class="brand-square" aria-hidden="true"></span>
      <span class="back-brand-name">IRONVALE</span>
    </div>
    <div class="service-lines">
      <p>Refining<span class="sep">•</span>Rail<span class="sep">•</span>Infrastructure<span class="sep">•</span>Mining</p>
      <p>Energy<span class="sep">•</span>Calgary<span class="sep">•</span>Edmonton<span class="sep">•</span>Fort McMurray</p>
      <p>Revelstoke<span class="sep">•</span>Vancouver</p>
    </div>
  </section>
</body>
</html>
```